Brochure and Business Card design

I am looking for a high end, elegant A4, 4 page brochure booklet to convey our products to clientele that will be visiting a luxury display showroom.

Harrowgate Locks and Grilles is a Australian security provider, and we supply high end products from reputable brands.
The brochure will be directed to clients building a new home with a partnered building company and will be accompanied with display boards of our products.

I am providing files of a document we have put together with the relevant information and some images to help along the way, we are not bound by the layout or style it has been drawn up and we wish to give you complete creative freedom putting the peaces together. I have also provided the files for our logo in two different colours, and a picture of a brochure we love the look of.

If you have any suggestions, we can likely come up with further images etc if it will help or even if you feel some should be removed, we are open to that also

Target Market(s)

Young familys, people building new luxury homes, proffesionals, home owners

Industry/Entity Type

Business

Font styles to use
Serif
Sans Serif

Requirements
Must have
• All 8 pages
Should not have
• Not really a fan of reds and similar.

```html
<!DOCTYPE html>
<html lang="en">
<head>
<meta charset="utf-8">
<title>Harrowgate Locks and Grilles – Brochure Spread</title>
<link rel="stylesheet" href="https://fonts.googleapis.com/css2?family=Didact+Gothic&family=Montserrat:wght@600;700&display=swap">
<style>
:root{
  --stage:#d0d0d0;
  --blue-top:#1b6fc4;
  --blue-bottom:#2ea7e6;
  --lime:#c9d600;
  --ring-blue:#1e8fd8;
  --green-panel:#93c123;
  --heading-green:#8dc63f;
  --ink:#555;
  --ink-dark:#333;
  --card-line:#e3e3e3;
  --white:#fff;
}
*{margin:0;padding:0;box-sizing:border-box}
html,body{width:1200px;height:645px;overflow:hidden;background:var(--stage)}
body{position:relative;font-family:"Didact Gothic",sans-serif;color:var(--ink)}
.page-label{position:absolute;top:91px;font-family:"Montserrat",sans-serif;font-weight:600;font-size:12px;color:#111}
.spread{position:absolute;left:81px;top:122px;width:1001px;height:388px;display:flex;background:var(--white)}
.panel{position:relative;height:100%}
.panel--alarm{width:232px;background:linear-gradient(180deg,var(--blue-top),var(--blue-bottom));color:var(--white)}
.panel--kits{width:269px}
.panel--intercom{width:224px;background:var(--green-panel);color:var(--white)}
.panel--products{width:276px}
.hero{position:absolute;left:21px;top:16px;width:170px;height:170px}
.panel-title{position:absolute;left:26px;font-size:29px;font-weight:400;letter-spacing:.2px}
.panel--alarm .panel-title{top:200px}
.panel--intercom .panel-title{top:208px}
.panel-body{position:absolute;left:26px;width:186px;font-size:6.4px;line-height:1.3;text-align:justify}
.panel-body p{margin-bottom:7px}
.panel--alarm .panel-body{top:240px}
.panel--intercom .panel-body{top:249px;width:178px}
.section-heading{font-family:"Montserrat",sans-serif;font-weight:700;color:var(--heading-green);font-size:10px}
.kits{position:absolute;left:17px;top:39px;width:236px}
.kits p{font-size:6.4px;line-height:1.3;margin-top:8px}
.kits .cta{font-weight:700;color:var(--ink-dark);margin-top:6px}
.upgrades-title{position:absolute;left:17px;top:136px;text-transform:uppercase;font-size:10.5px}
.upgrade-grid{position:absolute;left:17px;top:161px;width:236px;display:grid;grid-template-columns:107px 107px;column-gap:13px;row-gap:7px}
.upgrade-card{height:48px;border:1px solid var(--card-line);display:flex;align-items:center;gap:5px;padding:0 5px}
.upgrade-card .thumb{width:38px;height:34px;flex:none;border-radius:3px;background:linear-gradient(135deg,#eef0f2,#b9bec4)}
.upgrade-card span{font-family:"Montserrat",sans-serif;font-weight:600;font-size:6px;color:var(--ink-dark);line-height:1.25}
.product{position:absolute;left:18px;width:250px;display:flex;gap:13px}
.product .thumb{width:72px;height:44px;flex:none;background:linear-gradient(135deg,#f4f4f4,#b7b2a4);border-radius:2px;margin-top:4px}
.product h3{font-family:"Montserrat",sans-serif;font-weight:700;font-size:9px;color:var(--heading-green)}
.product p{font-size:6.1px;line-height:1.3;margin-top:2px;width:150px}
.product--one{top:34px}.product--two{top:113px}.product--three{top:200px}
.divider{position:absolute;left:105px;width:150px;border-top:1px solid #cfcfcf}
.divider--one{top:100px}.divider--two{top:188px}
.intercom-upgrades-title{position:absolute;left:28px;top:275px;text-transform:uppercase;font-size:10px}
.intercom-upgrades{position:absolute;left:31px;top:293px;display:flex;gap:5px}
.intercom-card{width:72px;height:79px;border:1px solid var(--card-line);display:flex;flex-direction:column;align-items:center;padding-top:8px}
.intercom-card .thumb{width:44px;height:42px;background:linear-gradient(135deg,#f2f2f2,#a9adb2);border-radius:2px}
.intercom-card span{font-family:"Montserrat",sans-serif;font-weight:600;font-size:5px;color:var(--ink-dark);text-align:center;line-height:1.3;margin-top:6px;padding:0 2px}
</style>
</head>
<body>
<div class="page-label" style="left:316px">Page 2</div>
<div class="page-label" style="left:828px">Page 3</div>

<main class="spread">
  <section class="panel panel--alarm">
    <svg class="hero" viewBox="0 0 170 170">
      <circle cx="91" cy="85" r="80" fill="var(--ring-blue)"/>
      <circle cx="82" cy="92" r="80" fill="var(--lime)"/>
      <circle cx="85" cy="82" r="80" fill="var(--white)"/>
      <circle cx="85" cy="82" r="76" fill="#3a3a3a" role="img" aria-label="Photo of an alarm keypad mounted on a dark wall"/>
    </svg>
    <h1 class="panel-title">Alarm Systems</h1>
    <div class="panel-body">
      <p>A Harrowgate Locks and Grilles alarm system with its state of the art equipment is the perfect defense for your family and home. With detection devices such as motion detectors, magnetic door sensors and warning devices like siren + strobe combos to alert others of a break in to name a few, it will be everything you need to feel secure.</p>
      <p>With the added option of having your security system monitored, you will always have someone watching over your home, even when even when the house is vacant..</p>
      <p>Did you know, industry leaders say that burglars are 3 times more likely to to target a home without a security system. This means that simply having a home security system always keeps you safer, even if an alarm is never triggered.</p>
    </div>
  </section>

  <section class="panel panel--kits">
    <div class="kits">
      <h2 class="section-heading">Home Kits</h2>
      <p>Standard kits consisting of everything you need to get an alarm up and running. Components such as an Alarm Control Panel, Keypad, 3 motion detectors, and internal siren, an external siren+strobe combo, battery back up incase the power goes out. A great starting platform that can be built on to your needs and requirements.</p>
      <p class="cta">Request a Security Advisor consultation for all the info.</p>
    </div>
    <h2 class="section-heading upgrades-title">Popular Upgrades</h2>
    <div class="upgrade-grid">
      <div class="upgrade-card"><div class="thumb" role="img" aria-label="OLED keypad"></div><span>OLED Keypad upgrade</span></div>
      <div class="upgrade-card"><div class="thumb" role="img" aria-label="Remote fobs and receiver board"></div><span>Remote Arm and Disarm</span></div>
      <div class="upgrade-card"><div class="thumb" role="img" aria-label="Monitoring communicator unit"></div><span>Professional Alarm Monitoring</span></div>
      <div class="upgrade-card"><div class="thumb" role="img" aria-label="Motion detector"></div><span>Motion Detectors' in additional rooms</span></div>
      <div class="upgrade-card"><div class="thumb" role="img" aria-label="Ceiling 360 degree motion detector"></div><span>360 degree motion detectors</span></div>
      <div class="upgrade-card"><div class="thumb" role="img" aria-label="Magnetic reed switch"></div><span>Door and window magnetic switches</span></div>
      <div class="upgrade-card"><div class="thumb" role="img" aria-label="Roller door magnetic switch"></div><span>Roller door magnetic switch</span></div>
    </div>
  </section>

  <section class="panel panel--intercom">
    <svg class="hero" viewBox="0 0 170 170" style="left:9px">
      <circle cx="91" cy="85" r="80" fill="var(--ring-blue)"/>
      <circle cx="82" cy="92" r="80" fill="var(--lime)"/>
      <circle cx="85" cy="82" r="80" fill="var(--white)"/>
      <circle cx="85" cy="82" r="76" fill="#d9c7b0" role="img" aria-label="Photo of a video intercom monitor on a warm wall"/>
    </svg>
    <h1 class="panel-title" style="left:30px">Intercom</h1>
    <div class="panel-body" style="left:24px">
      <p>A Harrowgate Locks and Grilles Intercom system is a great addition to any home. Giving you the ability to communicate with visitors to your home at your front door or even at your front gate. In conjunction with the use of an electric strike you can hit the door release button on the intercom and let them in from where you stand in the home. Maybe even better still, decide to not let them in.</p>
      <p>With the video intercom option your visitor will be displayed automatically and you can view who it is without them even knowing you are there.</p>
    </div>
  </section>

  <section class="panel panel--products">
    <div class="product product--one">
      <div class="thumb" role="img" aria-label="Colour video intercom kit with box"></div>
      <div><h3>KV Colour Video Intercom</h3><p>Superior quality, touch button control and door release. This sleek glass face 7' screen intercom is just what you need to visually see and communicate with who is at the front gate or door. With the add on addition of a extra monitor makes it perfect for two story homes with the extra station up stairs.</p></div>
    </div>
    <div class="divider divider--one"></div>
    <div class="product product--two">
      <div class="thumb" role="img" aria-label="Glass face video monitor and door station"></div>
      <div><h3>KL Colour Video Intercom</h3><p>All the smarts built into a compact, modern designed glass face monitor. This unit has touch screen control, inter home communication between monitors and a build in handset for minimal disturbance when required. With maximums of 4 door stations and 8 Monitors, this system is perfect for the homes with multiple entry points and when multiple room monitors are required.</p></div>
    </div>
    <div class="divider divider--two"></div>
    <div class="product product--three">
      <div class="thumb" role="img" aria-label="Audio door station and handset"></div>
      <div><h3>Audio Only Intercom</h3><p>Whether it's to help fit within the budget, and you just don't have the requirement of having to see who is at the door, this no fuss, single purpose audio only intercom is that handy addition to the living area.</p></div>
    </div>
    <h2 class="section-heading intercom-upgrades-title">Popular Upgrades</h2>
    <div class="intercom-upgrades">
      <div class="intercom-card"><div class="thumb" role="img" aria-label="Flush mount stainless door station"></div><span>Upgrade to flush mount stainless steel door station</span></div>
      <div class="intercom-card"><div class="thumb" role="img" aria-label="Electric strike"></div><span>Extend intercom wiring to property font gate</span></div>
      <div class="intercom-card"><div class="thumb" role="img" aria-label="Additional video monitor"></div><span>Additional monitor installed. (Video Only)</span></div>
    </div>
  </section>
</main>
</body>
</html>
```